Dental Implant Logo and Business Card for Local Dentist

Design a unique business card and a logo that incorporates a dental implant as a primary focal point or a part of the text. New logo design & business card needs to incorporate our businesses old star shaped logo (attached) and a dental implant, along with our business name. Star logo does not have to remain the exact same colors and can be any size. Looking for a warm, friendly (non-aggressive) design that uses colors in the blue-green palate, partial to mint-turquoise color similar to the images attached . SIMPLE IS GOOD, but looking for creativity to bring all the elements together. OK to incorporate a splash of color. I have attached a few images of implant logos I like along with our existing star shaped logo. *I have also uploaded some images that represent local landscapes & images for the back of the business card. I would like to include a silhouette or sketch that represents one one of these areas on the back of the business card to convey the connection to our community and local roots of our business since we are 4th generation members of this community . Can visit our dental practice website for more info. www.hartwellandodegarddentalcare.example Card Must Haves on Front of Card:1. business name "Hartwell & Odegard Dental Care" 2. My Name: "Colin Odegard D.D.S."3. Phone # (925) 754-6020Other info for card (can be front or back)Address: 7840 Quarry Ridge Rd. #2C Bramblecove, ST 94531e-mail: millerandsimarrodentalcare@gmail.comcosmetic, family, & impDesign a unique business card and a logo that incorporates a dental implant as a primary focal point or a part of the text. New logo design & business card needs to incorporate our businesses old star shaped logo (attached) and a dental implant, along with our business name. Star logo does not have to remain the exact same colors and can be any size. Looking for a warm, friendly (non-aggressive) design that uses colors in the blue-green palate, partial to mint-turquoise color similar to the images attached . SIMPLE IS GOOD, but looking for creativity to bring all the elements together. OK to incorporate a splash of color. I have attached a few images of implant logos I like along with our existing star shaped logo. *I have also uploaded some images that represent local landscapes & images for the back of the business card. I would like to include a silhouette or sketch that represents one one of these areas on the back of the business card to convey the connection to our community and local roots of our business since we are 4th generation members of this community . Can visit our dental practice website for more info. www.hartwellandodegarddentalcare.example Card Must Haves on Front of Card:1. business name "Hartwell & Odegard Dental Care" 2. My Name: "Colin Odegard D.D.S."3. Phone # (925) 754-6020Other info for card (can be front or back)Address: 7840 Quarry Ridge Rd. #2C Bramblecove, ST 94531e-mail: millerandsimarrodentalcare@gmail.comcosmetic, family, & implant dentistry

Target Market(s)

Families

Industry/Entity Type

Dental

Contact Information for Business Card

See Project description above

Logo Text

Hartwell & Odegard Dental Care

Font styles to use
Serif

Colors
ffffff
33b8a4
87cfc6
0492cd
33a6d7
0255a3

Requirements
Must have
• *See Description...
• Card Must Haves on Front of Card:
• 1. business name "Hartwell & Odegard Dental Care"
• 2. My Name: "Colin Odegard D.D.S."
• 3. Phone # (555) 318-4297
• Other info for card (can be front or back)
• Address: 7840 Quarry Ridge Rd. #2C Bramblecove, ST 90217
• e-mail: hartwellandodegarddentalcare@example-mail.com
Nice to have
• Local image sketch or silhouette on back side of business card with remaining information on back: address, website, e-mail etc.

```html
<!DOCTYPE html>
<html lang="en">
<head>
<meta charset="utf-8">
<title>Hartwell &amp; Odegard Dental Care – Business Card</title>
<link href="https://fonts.googleapis.com/css2?family=Cinzel:wght@500&family=Open+Sans:wght@400;600&display=swap" rel="stylesheet">
<style>
  :root {
    --bg: #d9dde2;
    --card-white: #ffffff;
    --brand-blue: #0255a3;
    --brand-teal: #33b8a4;
    --text-dark: #333a40;
    --slate-top: #47607a;
    --slate-mid: #55708a;
    --shore-green: #4c5a3e;
    --back-text: #eef2f5;
  }
  * { margin: 0; padding: 0; box-sizing: border-box; }
  html, body { width: 1200px; height: 900px; overflow: hidden; }
  body {
    background: var(--bg);
    font-family: "Open Sans", Arial, sans-serif;
    position: relative;
  }
  .card {
    position: absolute;
    left: 240px;
    width: 720px;
    height: 410px;
    border-radius: 22px;
    overflow: hidden;
    box-shadow: 0 8px 24px rgba(0,0,0,.18);
  }
  .card--front { top: 40px; background: var(--card-white); }
  .card--back { top: 470px; }

  /* front */
  .brand-lockup {
    position: absolute;
    left: 30px; top: 150px;
    width: 250px;
    text-align: center;
  }
  .brand-dot {
    width: 40px; height: 40px;
    border-radius: 50%;
    background: var(--brand-teal);
    margin: 0 auto 14px;
  }
  .brand-name {
    font-family: "Cinzel", Georgia, serif;
    font-weight: 500;
    font-size: 19px;
    line-height: 1.3;
    color: var(--brand-blue);
    letter-spacing: .5px;
  }
  .divider {
    position: absolute;
    left: 300px; top: 70px;
    width: 2px; height: 270px;
    background: var(--brand-blue);
  }
  .details {
    position: absolute;
    left: 330px; top: 80px;
    width: 370px;
    color: var(--text-dark);
  }
  .person-name {
    font-size: 34px;
    font-weight: 400;
    color: var(--brand-blue);
    line-height: 1.1;
  }
  .person-title { font-size: 16px; margin: 4px 0 14px; }
  .address { font-size: 16px; line-height: 1.35; margin-bottom: 12px; }
  .contact-list { list-style: none; font-size: 14px; line-height: 1.6; }
  .contact-list li { display: flex; align-items: center; gap: 8px; white-space: nowrap; }
  .contact-list svg { width: 12px; height: 12px; flex: none; }

  /* back */
  .landscape {
    position: absolute; inset: 0;
    background: linear-gradient(180deg, var(--slate-top) 0%, var(--slate-mid) 55%, #5d6f66 72%, var(--shore-green) 100%);
  }
  .back-name {
    position: absolute;
    right: 40px; top: 50px;
    font-family: "Cinzel", Georgia, serif;
    font-weight: 500;
    font-size: 26px;
    color: var(--back-text);
    text-align: right;
    line-height: 1.3;
    letter-spacing: 1px;
  }
</style>
</head>
<body>
  <section class="card card--front" aria-label="Business card front">
    <div class="brand-lockup">
      <div class="brand-dot"></div>
      <div class="brand-name">Hartwell &amp; Odegard<br>Dental Care</div>
    </div>
    <div class="divider"></div>
    <div class="details">
      <h1 class="person-name">Colin Odegard D.D.S.</h1>
      <p class="person-title">Director</p>
      <p class="address">7840 Quarry Ridge Rd.<br>#2C Bramblecove, ST 90217</p>
      <ul class="contact-list">
        <li>
          <svg viewBox="0 0 12 12"><path d="M3 1 L5 3.5 L4 5 Q5 7 7 8 L8.5 7 L11 9 L9.5 11 Q4 10.5 1 3 Z" fill="var(--brand-blue)"/></svg>
          (555) 318-4297
        </li>
        <li>
          <svg viewBox="0 0 12 12"><rect x="1" y="2.5" width="10" height="7" fill="none" stroke="var(--brand-blue)" stroke-width="1.2"/><path d="M1 2.5 L6 6.5 L11 2.5" fill="none" stroke="var(--brand-blue)" stroke-width="1.2"/></svg>
          hartwellandodegarddentalcare@example-mail.com
        </li>
        <li>
          <svg viewBox="0 0 12 12"><circle cx="6" cy="6" r="5" fill="none" stroke="var(--brand-blue)" stroke-width="1.2"/><ellipse cx="6" cy="6" rx="2.2" ry="5" fill="none" stroke="var(--brand-blue)" stroke-width="1"/><path d="M1 6 H11" stroke="var(--brand-blue)" stroke-width="1"/></svg>
          www.hartwellandodegarddentalcare.example
        </li>
      </ul>
    </div>
  </section>

  <section class="card card--back" aria-label="Business card back">
    <div class="landscape" role="img" aria-label="Local lakeside landscape with hills, water, rocky shore and grass under a slate blue tint"></div>
    <div class="back-name">Hartwell &amp; Odegard<br>Dental Care</div>
  </section>
</body>
</html>
```